Web Banner Ads for Velorin Baby Monitor

Velorin is a top selling security camera company that is currently #1 best sellers on several categories on Quillmart. We have just released a new Velorin Baby Monitor and are in need of web banner ads for the Velorin baby Monitor that will be placed on Quillmart Promotion Networks that will be displayed throughout Quillmart.

We would like for the designer to provide Ads that can display some of the features and functionality of the baby monitor and camera, while still maintaining a modern, slick and simple style. The banners can have a tag line but should share the same theme of watching over your loved one.

There will need to be several different sizes that must be exact and adhere strictly to the guidelines below. If the creatives are off by even a little bit or are over the file size they will be kicked back. I have submitted a sample of another add for one of our Wifi cameras as well.

Please have a look at the listing below for more information on the product.

https://www.quillmart-shop.example/Velorin-Monitor-Night-Vision-Camera/dp/K58PZ3RT4M

Target Market(s)

Quillmart, online shoppers, parents, new parents, mothers, home owners, pet owners.

Industry/Entity Type

Baby Care

Number of Pages Required

1 page

Requirements
Must have
• All of the dimensions required in the attached files. We will also need the creatives submitted as JPEGs adhering to the exact size and dimensions as well as the PSD files.

```html
<!DOCTYPE html>
<html lang="en">
<head>
<meta charset="utf-8">
<title>Velorin Baby Monitor – Web Banner 1200×148</title>
<link rel="stylesheet" href="https://fonts.googleapis.com/css2?family=Montserrat:wght@400;500&family=Oswald:wght@600&family=Roboto:wght@400;500&display=swap">
<style>
  :root {
    --sky-light: #5ccdf3;
    --sky-deep: #27b3e6;
    --panel-white: #ffffff;
    --navy: #1b2350;
    --photo-cream: #f4e8dc;
    --photo-warm: #e8cdb4;
    --product-white: #eef1f4;
    --product-shade: #c9d0d8;
    --text-white: #ffffff;
  }
  html, body {
    margin: 0;
    padding: 0;
    width: 1200px;
    height: 148px;
    overflow: hidden;
    background: #ffffff;
  }
  .banner {
    position: relative;
    width: 1200px;
    height: 148px;
    overflow: hidden;
    background: linear-gradient(180deg, var(--sky-light) 0%, var(--sky-deep) 100%);
    font-family: "Roboto", Arial, sans-serif;
  }
  .brand {
    position: absolute;
    left: 25px;
    top: 30px;
    display: flex;
    align-items: center;
    gap: 12px;
    color: var(--text-white);
  }
  .brand-dot {
    width: 22px;
    height: 22px;
    border: 2.5px solid var(--text-white);
    border-radius: 50%;
    box-sizing: border-box;
  }
  .brand-name {
    font-family: "Montserrat", Arial, sans-serif;
    font-weight: 500;
    font-size: 22px;
    letter-spacing: 9px;
    text-transform: uppercase;
  }
  .shop-button {
    position: absolute;
    left: 66px;
    top: 82px;
    width: 119px;
    height: 35px;
    box-sizing: border-box;
    border: 1.5px solid var(--text-white);
    border-radius: 18px;
    color: var(--text-white);
    font-family: "Roboto", Arial, sans-serif;
    font-weight: 500;
    font-size: 13.5px;
    letter-spacing: 0.3px;
    display: flex;
    align-items: center;
    justify-content: center;
    text-decoration: none;
  }
  .panel {
    position: absolute;
    left: 0;
    top: 0;
  }
  .headline {
    position: absolute;
    left: 590px;
    top: 28px;
    width: 372px;
    margin: 0;
    text-align: center;
    font-family: "Oswald", "Arial Narrow", sans-serif;
    font-weight: 600;
    font-size: 31px;
    line-height: 40px;
    color: var(--navy);
    letter-spacing: 0.2px;
  }
  .features {
    position: absolute;
    left: 590px;
    top: 78px;
    width: 372px;
    margin: 0;
    padding: 0;
    list-style: none;
    text-align: center;
    color: var(--navy);
    font-size: 14px;
    line-height: 26px;
    letter-spacing: 0.2px;
  }
  .product-image {
    position: absolute;
    left: 1071px;
    top: 12px;
    width: 84px;
    height: 128px;
    border-radius: 40px 40px 10px 10px;
    background: linear-gradient(160deg, var(--product-white) 0%, var(--product-shade) 100%);
  }
  .model-code {
    position: absolute;
    right: 8px;
    bottom: 8px;
    font-size: 9px;
    font-weight: 500;
    color: var(--text-white);
  }
</style>
</head>
<body>
  <div class="banner">
    <div class="brand">
      <span class="brand-dot"></span>
      <span class="brand-name">Velorin</span>
    </div>
    <a class="shop-button" href="#">SHOP NOW</a>

    <svg class="panel" width="1200" height="148" viewBox="0 0 1200 148">
      <defs>
        <linearGradient id="photoTone" x1="0" y1="0" x2="1" y2="0">
          <stop offset="0" stop-color="var(--photo-warm)"/>
          <stop offset="0.55" stop-color="var(--photo-cream)"/>
          <stop offset="1" stop-color="#ffffff"/>
        </linearGradient>
      </defs>
      <polygon points="284,7 1022,7 989,144 272,144" fill="var(--panel-white)"/>
      <polygon points="284,7 590,7 590,144 272,144" fill="url(#photoTone)"
               role="img" aria-label="Photo of a sleeping newborn baby hugging a teddy bear on a soft white blanket"/>
    </svg>

    <h1 class="headline">BE THERE EVEN IF YOU'RE NOT</h1>
    <ul class="features">
      <li>PAN/TILT BABY MONITOR AND CAMERA</li>
      <li>PAN/TILT BABY MONITOR WITH NIGHT VISION</li>
    </ul>

    <div class="product-image" role="img" aria-label="Product photo of the white pan/tilt baby monitor camera"></div>
    <span class="model-code">C7</span>
  </div>
</body>
</html>
```